BUSINESS CARD - HALLORAN FIELD SERVICES

I would like to create a business card for my fertilizer spreading business. I would like to incorporate my existing logo and also a description of the services offered. The business card will be given to farmers so must be kept simple but effective. It will also be left in stores so much also be eye catching in order to stand out from other cards.

Target Market(s)

FARMERS

Requirements
Must have
• FRONT OF CARD = EXISTING LOGO + "CUSTOMISED SPREADING" below the logo

REAR Of CARD = SERVICES OFFERED AND CONTACT DETAILS

- Bulk fertilizer including Lime, Gypsum, Manure & Compost
- Granular fertilizer including Single Super, Urea, Gran-am, & Custom Blends
- Modern equipment - Autosteer & Variable Rate Capable
- Friendly & Reliable Service
- Contact Gus: 0417 552 308
Nice to have
• utilize same color scheme as existing logo

```html
<!DOCTYPE html>
<html lang="en">
<head>
<meta charset="utf-8">
<title>Halloran Field Services – Business Card</title>
<link rel="stylesheet" href="https://fonts.googleapis.com/css2?family=Oswald:wght@500&family=Lato:ital,wght@0,400;0,700;0,900;1,400&display=swap">
<style>
  :root {
    --orange: #f7941d;
    --orange-soft: #fbc27a;
    --charcoal: #4a4a4c;
    --paper: #ffffff;
    --backdrop: #e4e4e6;
  }
  * { box-sizing: border-box; margin: 0; padding: 0; }
  html, body {
    width: 1200px; height: 1200px; overflow: hidden;
    background: var(--backdrop);
    font-family: "Lato", Arial, sans-serif;
  }
  .stage { position: relative; width: 1200px; height: 1200px; }
  .card {
    position: absolute; width: 480px; height: 840px;
    background: var(--paper); overflow: hidden;
  }
  .card--front { left: 96px; top: 78px; }
  .card--back  { left: 630px; top: 288px; }

  /* brand lockup */
  .brand { position: absolute; left: 0; right: 0; text-align: center; color: var(--charcoal); font-weight: 700; z-index: 2; }
  .brand__ring { display: block; margin: 0 auto; }
  .brand__name { line-height: 1.05; letter-spacing: -0.5px; }
  .card--front .brand { top: 46px; }
  .card--front .brand__name { font-size: 44px; margin-top: 14px; }
  .card--back .brand { top: 34px; }
  .card--back .brand__name { font-size: 30px; margin-top: 10px; }

  /* front headline */
  .headline {
    position: absolute; left: 0; right: 0; top: 340px;
    text-align: center; font-family: "Oswald", "Arial Narrow", sans-serif;
    font-weight: 500; font-size: 92px; line-height: 1.08; letter-spacing: 1px;
  }
  .headline__top { color: var(--orange); display: block; }
  .headline__bottom { color: var(--charcoal); display: block; }

  /* field artwork areas */
  .field {
    position: absolute; left: 0; right: 0; bottom: 0;
    background: linear-gradient(to bottom, rgba(247,148,29,0) 0%, var(--orange-soft) 30%, var(--orange) 60%, var(--orange) 100%);
  }
  .card--front .field { height: 250px; }
  .card--back .field  { height: 320px; }
  .wheat {
    position: absolute; right: -60px; top: 160px; width: 260px; height: 560px;
    background: radial-gradient(closest-side, rgba(247,148,29,0.28) 0%, rgba(247,148,29,0.12) 55%, rgba(247,148,29,0) 100%);
  }

  /* contact */
  .contact {
    position: absolute; left: 0; right: 0; text-align: center;
    font-weight: 900; font-size: 40px; letter-spacing: 0.5px; z-index: 2;
  }
  .contact__icon { display: block; margin: 0 auto 10px; }
  .card--front .contact { bottom: 22px; color: var(--paper); }
  .card--back .contact {
    bottom: 24px; color: var(--charcoal); font-size: 38px;
    display: flex; align-items: center; justify-content: center; gap: 12px;
  }
  .card--back .contact__icon { margin: 0; }

  /* services list */
  .services { position: absolute; left: 24px; right: 20px; top: 228px; list-style: none; z-index: 2; }
  .service { position: relative; padding-left: 40px; margin-bottom: 14px; }
  .service__mark { position: absolute; left: 0; top: 5px; }
  .service__title { color: var(--orange); font-weight: 900; font-size: 22px; letter-spacing: 0.3px; line-height: 1.2; }
  .service__detail { color: var(--charcoal); font-size: 21px; line-height: 1.3; }
  .service__detail em { font-style: italic; }
</style>
</head>
<body>
<main class="stage">

  <!-- FRONT -->
  <section class="card card--front" aria-label="Business card front">
    <div class="brand">
      <svg class="brand__ring" width="150" height="150" viewBox="0 0 150 150" aria-hidden="true">
        <circle cx="75" cy="75" r="68" fill="none" stroke="var(--charcoal)" stroke-width="8"/>
      </svg>
      <p class="brand__name">Halloran Field Services</p>
    </div>

    <h1 class="headline">
      <span class="headline__top">CUSTOMIZED</span>
      <span class="headline__bottom">SPREADING</span>
    </h1>

    <div class="field" role="img" aria-label="Orange silhouette of tall field grass rising into a solid orange band"></div>

    <p class="contact">
      <svg class="contact__icon" width="34" height="34" viewBox="0 0 34 34" aria-hidden="true">
        <circle cx="17" cy="17" r="17" fill="var(--charcoal)"/>
        <path d="M12 9.5c1-.6 2 .1 2.5 1.2l1 2.2c.4.9 0 1.6-.7 2.1l-.8.6c.7 1.8 2 3.2 3.8 4.1l.7-.8c.6-.7 1.300-.9 2.1-.5l2.2 1c1.1.5 1.6 1.6 1 2.6-.8 1.4-2.2 2.2-3.8 1.8-5-1.4-8.7-5.2-9.8-10.2-.3-1.6.5-3.4 1.8-4.1z" fill="var(--paper)"/>
      </svg>
      GUS 0417 552 308
    </p>
  </section>

  <!-- BACK -->
  <section class="card card--back" aria-label="Business card back">
    <div class="wheat" role="img" aria-label="Orange wheat stalks standing at the right edge"></div>
    <div class="field" role="img" aria-label="Orange silhouette of field grass rising into a solid orange band"></div>

    <div class="brand">
      <svg class="brand__ring" width="104" height="104" viewBox="0 0 104 104" aria-hidden="true">
        <circle cx="52" cy="52" r="47" fill="none" stroke="var(--charcoal)" stroke-width="6"/>
      </svg>
      <p class="brand__name">Halloran Field Services</p>
    </div>

    <ul class="services">
      <li class="service">
        <svg class="service__mark" width="28" height="16" viewBox="0 0 28 16" aria-hidden="true"><path d="M2 3l12 10L26 3" fill="none" stroke="var(--orange)" stroke-width="4" stroke-linecap="round" stroke-linejoin="round"/></svg>
        <p class="service__title">BULK FERTILIZER</p>
        <p class="service__detail"><em>including</em> Lime, Gypsum,<br>Manure &amp; Compost</p>
      </li>
      <li class="service">
        <svg class="service__mark" width="28" height="16" viewBox="0 0 28 16" aria-hidden="true"><path d="M2 3l12 10L26 3" fill="none" stroke="var(--orange)" stroke-width="4" stroke-linecap="round" stroke-linejoin="round"/></svg>
        <p class="service__title">MODERN EQUIPMENT</p>
        <p class="service__detail">Autosteer &amp;<br>Variable Rate Capable</p>
      </li>
      <li class="service">
        <svg class="service__mark" width="28" height="16" viewBox="0 0 28 16" aria-hidden="true"><path d="M2 3l12 10L26 3" fill="none" stroke="var(--orange)" stroke-width="4" stroke-linecap="round" stroke-linejoin="round"/></svg>
        <p class="service__title">GRANULAR FERTILIZER</p>
        <p class="service__detail"><em>including</em> Single Super, Urea,<br>Gran-am, &amp; Custom Blends</p>
      </li>
      <li class="service">
        <svg class="service__mark" width="28" height="16" viewBox="0 0 28 16" aria-hidden="true"><path d="M2 3l12 10L26 3" fill="none" stroke="var(--orange)" stroke-width="4" stroke-linecap="round" stroke-linejoin="round"/></svg>
        <p class="service__title">FRIENDLY &amp; RELIABLE<br>SERVICES</p>
      </li>
    </ul>

    <p class="contact">
      <svg class="contact__icon" width="34" height="34" viewBox="0 0 34 34" aria-hidden="true">
        <circle cx="17" cy="17" r="17" fill="var(--charcoal)"/>
        <path d="M12 9.5c1-.6 2 .1 2.5 1.2l1 2.2c.4.9 0 1.6-.7 2.1l-.8.6c.7 1.8 2 3.2 3.8 4.1l.7-.8c.6-.7 1.3-.9 2.1-.5l2.2 1c1.1.5 1.6 1.6 1 2.6-.8 1.4-2.2 2.2-3.8 1.8-5-1.4-8.7-5.2-9.8-10.2-.3-1.6.5-3.4 1.8-4.1z" fill="var(--paper)"/>
      </svg>
      GUS 0417 552 308
    </p>
  </section>

</main>
</body>
</html>
```